New Business Card Design Project

Need a design that will create an impact / strong impression towards our clients for our business. We are in the lighting business and we do lighting retrofits for large commercial to industrial clientele.

Target Market(s)

Lighting Industry

Industry/Entity Type

Business

Font styles to use
Other font styles liked:
• we would like to use the font on our logo, not sure what it is though..

Requirements
Must have
• Our logo.
Nice to have
• We are open to suggestions that have to do with lighting.

```html
<!DOCTYPE html>
<html lang="en">
<head>
<meta charset="utf-8">
<title>Halvern Lighting Partners – Business Card</title>
<link href="https://fonts.googleapis.com/css2?family=Roboto:wght@400;500&family=Roboto+Condensed:wght@500&display=swap" rel="stylesheet">
<style>
  :root {
    --backdrop: #5a4939;
    --paper: #f1f1f1;
    --forest: #123d12;
    --leaf: #5dbb55;
    --title-green: #6ec24e;
    --name-green: #2fa043;
    --brand-dark: #1b5e20;
    --back-green: #0a7f35;
    --ink-light: #f4f4f4;
  }
  * { margin: 0; padding: 0; box-sizing: border-box; }
  html, body { width: 1200px; height: 960px; overflow: hidden; }
  body {
    background: var(--backdrop);
    font-family: "Roboto", Arial, sans-serif;
    position: relative;
  }
  .card {
    position: absolute;
    width: 597px;
    height: 343px;
    overflow: hidden;
  }
  .card--front { left: 314px; top: 113px; background: var(--paper); }
  .card--back { left: 312px; top: 472px; background: var(--back-green); }

  .front-panel { position: absolute; inset: 0; }

  .brand {
    position: absolute;
    left: 46px;
    top: 48px;
    display: flex;
    align-items: center;
    gap: 10px;
    color: var(--brand-dark);
    font-weight: 500;
    font-size: 17px;
    letter-spacing: 0.5px;
    line-height: 1.15;
  }
  .brand-square {
    width: 34px; height: 34px;
    background: var(--brand-dark);
    flex: none;
  }

  .person {
    position: absolute;
    right: 31px;
    top: 46px;
    text-align: right;
    font-family: "Roboto Condensed", Arial, sans-serif;
    font-weight: 500;
  }
  .person-name { color: var(--name-green); font-size: 23px; line-height: 1.1; }
  .person-title { color: var(--title-green); font-size: 16.5px; margin-top: 3px; }

  .address {
    position: absolute;
    right: 31px;
    top: 162px;
    text-align: right;
    color: var(--ink-light);
    font-size: 15px;
    font-style: normal;
    line-height: 18px;
  }
  .contacts {
    position: absolute;
    right: 32px;
    top: 208px;
    list-style: none;
    color: var(--ink-light);
    font-size: 15px;
    line-height: 19.3px;
  }
  .contacts li { display: flex; justify-content: flex-end; align-items: center; gap: 7px; }
  .contacts svg { width: 13px; height: 13px; fill: var(--name-green); flex: none; }

  .back-brand {
    position: absolute;
    left: 0; right: 0;
    top: 142px;
    display: flex;
    justify-content: center;
    align-items: center;
    gap: 14px;
    color: #ffffff;
    font-weight: 500;
    font-size: 30px;
    letter-spacing: 2px;
  }
  .back-square { width: 40px; height: 40px; background: #ffffff; }
  .back-url {
    position: absolute;
    left: 0; right: 0;
    top: 282px;
    text-align: center;
    color: var(--ink-light);
    font-size: 14px;
    letter-spacing: 3px;
  }
</style>
</head>
<body>

<section class="card card--front">
  <svg class="front-panel" viewBox="0 0 597 343" aria-hidden="true">
    <polygon points="440,0 597,0 597,343 183,343" fill="var(--forest)"/>
    <polygon points="430,0 440,0 183,343 173,343" fill="var(--leaf)"/>
    <polygon points="433.5,0 436.5,0 179.5,343 176.5,343" fill="var(--paper)"/>
  </svg>

  <div class="brand">
    <span class="brand-square"></span>
    <span>HALVERN<br>LIGHTING PARTNERS, INC.</span>
  </div>

  <div class="person">
    <div class="person-name">DANIEL MARSH</div>
    <div class="person-title">CEO/FOUNDER</div>
  </div>

  <address class="address">
    2140 Cedarbrook Road<br>Fairview, Oregon 97024
  </address>

  <ul class="contacts">
    <li>503 214 7781
      <svg viewBox="0 0 16 16"><path d="M3.6 1.2l2.3 2.6-1.3 1.9c.9 2 2.6 3.7 4.6 4.6l1.9-1.3 2.6 2.3-1.4 2.4C7 13.4 2.6 9 1.2 3z"/></svg></li>
    <li>503 662 0195
      <svg viewBox="0 0 16 16"><path d="M4 0h8v16H4zM5.3 1.5v11h5.4v-11zM7 13.6h2v1.2H7z" fill-rule="evenodd"/></svg></li>
    <li>503 214 7790
      <svg viewBox="0 0 16 16"><path d="M4 2h8v3H4zM1 6h14v6h-3v2H4v-2H1zM5 10v2.5h6V10z" fill-rule="evenodd"/></svg></li>
    <li>daniel@halvernlight.com
      <svg viewBox="0 0 16 16"><path d="M1 3h14v1L8 9 1 4zM1 5.5l7 5 7-5V13H1z"/></svg></li>
    <li>www.halvernlight.com
      <svg viewBox="0 0 16 16"><circle cx="8" cy="8" r="7"/><path d="M5 4c2 1 1 3 3 3s1 3-1 4M10 3c0 2 2 2 3 3" stroke="var(--forest)" stroke-width="1.3" fill="none"/></svg></li>
  </ul>
</section>

<section class="card card--back">
  <div class="back-brand">
    <span class="back-square"></span>
    <span>HALVERN</span>
  </div>
  <div class="back-url">www.halvernlightingpartners.com</div>
</section>

</body>
</html>
```